Web Design job: SaaS start-up needs a cutting-edge web design

What's Needed:
- All designs files created
- Fully coded implementation in HTML/CSS/Bootstrap
- Pages: 5 -- see content here http://www.TeamVerdexa.com
-- Home Page
-- The Hidden Value
-- Benefits
-- About us
-- Careers
- The existing site has the textual content for each page. We can tweak to meet specific designs if needed.
- You will need to update/create image and interactive content for pages.

Reference:
Our existing website has a lot of content on it for reference -
http://www.TeamVerdexa.com

Description:
We need a web design that focuses in the UX and conveys the idea of magically fixing company problems by way of using our software.

Home Page
The main goal is to Drive Sales of the SaaS tool. When a visitor lands on our home page they should see: What we do, How we can help their problem and How to contact us.
1. Quickly understand What We Do
-- we sell SaaS software.
-- Need to quickly convey what our software does. It's seems complicated but really its not. See the description in about us for more info and visit our existing site.

2. How we can help their problem
-- We aim to solve any problem related to employees
-- Even if the visitor does not have a specific problem in mind, there are several areas organizations can always improve: (some examples below)
---- Create Stronger, More Productive Teams
---- Build Better Communications Pathways
---- Encourage Innovation and Positive Change
---- Develop and Retain Strong "Company Culture"

3. Be able to Contact Us to get started
-- contacting us to get a sales lead is the ultimate goal.
-- the user should not have to hunt to contact us. needs to be easy.

Other Pages (Hidden Value, Benefit, About Us, Careers):
-- These are informative pages about our software and process.
-- If we grab the attention of the user on the home page then these are the pages that they will explore for more info.
-- Should be able to link to these pages from the main nav or from sections with the homepage. For example: What We Do sections could link to the benefits page. How we help their problem sections could link to the Hidden Value page. Regardless of what links to where, the idea is that we will be able to nav to other areas.

About Us:
Our company name is TeamVerdexa (as in Organizational Analysis). We provide a software as a service (SaaS) that uses a simple 6-question survey to analyze the relationships of people within an Organization and provide leaders with ground-breaking Insights about their teams, interactive social network data visualizations to explore their team's composition and we give detailed profiles of the key players (i.e, who are the Social Bridges, Who are the Knowledge Bottlenecks, Who are the Best Mentors, Who are the people that are completely disconnected/out of the loop). Leaders then use this information to make high level organizational decisions.

What's unique about our software:
-- Powerful analysis results from just a 6-question "pulse-surveys"
-- Innovative Tools for visually exploring the organization through relationships as opposed to org-chart
-- Get real-time results as opposed to waiting months with traditional methods
-- Traditional Org-charts represent the organization's skeleton, whereas we uncover the organization's neural network (how it solves problems).

Preferred fonts (but could be convinced otherwise if looks great):
-- Section titles - Aleo
-- Main body - Lato
-- TeamVerdexa logo - Philosopher

Things we like:
-- We like a big slider as the top of the landing page.

Colors to include:
-- Colors in the logo (red, blue, green, teal) as accent colors

Feel of the site:
-- Cutting-edge Software
-- Professional
-- Social Network flare (we analyze relationships)

Note:
If we find a great match with a designer there is strong possibility to continue the relationship with follow on work redesigning our web-based application.

Target Market(s)

Current customers are Morrow Pike & Fenwell, Clearbrook Valley Bank.
We target anyone that manages a large team. Such as Corporate Leaders, High Level Managers, HR Leaders

Industry/Entity Type

Business Software

Contact Information for Business Card

Logo image
Name of company "TEAMVERDEXA" In Philosopher font.
Tagline: "Unlock the Hidden Value In Your Teams"
Person's Name, Title, email, phone.

Coding

Coded - Design and coding required

Number of Pages Required

4 page

Font styles to use
Other font styles liked:
• Lato, Philosopher, Aero

Colors
ec1f27
0255a3

Requirements
Must have
• See description.
Nice to have
• Things we like:
• We like a big slider as the top of the landing page. Ours is a little clunky and outdated but something fresh and sleek would be great.
• Colors to include:
• We would like to use the colors in the logo as accent colors in the site to give a consistent look and feel.
• Feel of the site:
• Cutting-edge Software
• Professional
• Social Network flare (we analyze relationships)

```html
<!DOCTYPE html>
<html lang="en">
<head>
<meta charset="utf-8">
<title>TeamVerdexa – Home</title>
<link rel="stylesheet" href="https://fonts.googleapis.com/css2?family=Aleo:wght@300;400&family=Lato:wght@400;700&display=swap">
<style>
:root{
  --red:#ec2327;
  --sky:#86cbe6;
  --ink:#2b2b2b;
  --text:#555;
  --muted:#8a8a8a;
  --line:#e4e4e4;
  --paper:#ffffff;
  --soft:#f7f7f7;
  --footer:#26262c;
  --footer-deep:#1d1d22;
  --footer-text:#d8d8d8;
  --blue:#0255a3;
  --green:#6ab04c;
  --teal:#2aa7a0;
}
*{margin:0;padding:0;box-sizing:border-box}
html,body{width:670px;height:1200px;overflow:hidden;background:var(--paper)}
body{position:relative;font-family:"Lato",sans-serif;color:var(--text)}
.abs{position:absolute}
.title{font-family:"Aleo",serif;font-weight:300;color:var(--ink);text-align:center;width:670px;left:0}

/* hero slider */
.hero{left:0;top:0;width:670px;height:361px;background:linear-gradient(100deg,#3d3f43 0%,#6a6560 40%,#8b7a66 60%,#5d5f63 100%)}
.hero-shade{left:0;top:0;width:670px;height:361px;background:rgba(25,28,34,.35)}
.logo{left:50px;top:14px;display:flex;align-items:center;gap:6px}
.logo-mark{width:18px;height:18px;border-radius:50%;background:var(--red)}
.logo-name{font-family:"Lato",sans-serif;font-weight:700;font-size:13px;color:#fff;letter-spacing:.5px}
.nav{top:21px;left:266px;display:flex;gap:20px;font-size:8px;color:#fff}
.login{left:544px;top:15px;width:75px;height:22px;border-radius:11px;background:var(--red);color:#fff;font-size:8px;line-height:22px;text-align:center}
.nav-rule{left:51px;top:47px;width:568px;height:1px;background:rgba(255,255,255,.25)}
.slide-title{top:162px;font-family:"Aleo",serif;font-weight:400;font-size:26px;color:var(--sky);text-align:center;width:670px}
.slide-sub{top:195px;font-family:"Aleo",serif;font-weight:300;font-size:13px;color:#fff;text-align:center;width:670px}
.btn-light{left:294px;top:221px;width:82px;height:22px;border-radius:11px;background:#fff;color:var(--ink);font-size:8px;line-height:22px;text-align:center}
.slider-arrow{top:172px;width:34px;height:42px;background:rgba(30,30,30,.45);color:#fff;font-size:10px;line-height:42px;text-align:center}
.slide-thumb{left:587px;top:172px;width:50px;height:41px;background:linear-gradient(135deg,#c9d2da,#4d5a68);border:1px solid #fff}
.scroll-down{left:320px;top:345px;width:30px;height:30px;border-radius:50%;background:#fff;box-shadow:0 1px 4px rgba(0,0,0,.15)}

/* shared */
.ornament{left:0;width:670px;height:10px}
.btn-outline{border:1px solid #d7d7d7;border-radius:12px;color:var(--ink);font-size:8px;text-align:center;background:#fff}
.rule{left:51px;width:568px;height:1px;background:var(--line)}

/* what we do */
.net-deco-left{left:0;top:362px;width:100px;height:134px;background:radial-gradient(circle at 30% 40%,rgba(106,176,76,.28),rgba(140,110,220,.14) 55%,transparent 75%)}
.net-deco-right{left:576px;top:436px;width:94px;height:116px;background:radial-gradient(circle at 70% 60%,rgba(170,60,160,.24),rgba(90,90,220,.12) 55%,transparent 75%)}
.intro{top:447px;left:85px;width:500px;text-align:center;font-size:8.6px;line-height:14px;color:var(--text);white-space:nowrap}

/* help */
.team-photo{left:0;top:608px;width:292px;height:146px;background:linear-gradient(90deg,#ededed,#c9a889 35%,#8fa7c3 70%,#f4f4f4)}
.benefits{left:330px;top:644px;list-style:none;font-size:8.6px;color:var(--text)}
.benefits li{height:16.5px;display:flex;align-items:center;gap:7px}
.benefits svg{flex:none}

/* contact */
.contact{left:0;top:754px;width:670px;height:266px;background:var(--soft)}
.contact-lead{top:831px;width:670px;text-align:center;font-size:8.6px;color:var(--text)}
.field{background:#fff;border:1px solid #e2e2e2;font-size:7.5px;color:var(--muted);padding:8px 12px}
.submit{left:278px;top:958px;width:104px;height:24px;border-radius:12px;background:var(--red);color:#fff;font-size:8px;line-height:24px;text-align:center}

/* footer */
.footer{left:0;top:1020px;width:670px;height:152px;background:var(--footer)}
.footer-title{top:1045px;width:670px;text-align:center;font-family:"Aleo",serif;font-weight:300;font-size:13px;color:#fff}
.office{top:1094px;color:var(--footer-text)}
.office-city{font-family:"Aleo",serif;font-weight:300;font-size:10.5px;color:#fff;margin-bottom:5px}
.office-line{display:flex;align-items:center;gap:6px;font-size:7px;height:12px}
.office-divider{top:1086px;width:1px;height:66px;background:#3c3c43}
.bottom-bar{left:0;top:1172px;width:670px;height:28px;background:var(--footer-deep)}
.copyright{left:50px;top:1182px;font-size:7px;color:#cfcfcf}
.bottom-nav{top:1182px;left:492px;display:flex;gap:12px;font-size:7px;color:#cfcfcf}
.to-top{left:637px;top:1163px;width:18px;height:18px;border-radius:50%;background:var(--red)}
</style>
</head>
<body>

<!-- hero slider -->
<div class="abs hero" role="img" aria-label="Photo of three colleagues smiling around a laptop in a bright office"></div>
<div class="abs hero-shade"></div>
<div class="abs logo"><span class="logo-mark"></span><span class="logo-name">TEAMVERDEXA</span></div>
<nav class="abs nav"><span>Home</span><span>The Hidden Value</span><span>Benefits</span><span>About Us</span><span>Careers</span></nav>
<div class="abs login">Client Login</div>
<div class="abs nav-rule"></div>
<div class="abs slider-arrow" style="left:0">&#8249;</div>
<div class="abs slider-arrow" style="left:638px">&#8250;</div>
<div class="abs slide-thumb" role="img" aria-label="Thumbnail of the next slide: two colleagues at a desk"></div>
<h1 class="abs slide-title">Fast and Easy Assessments</h1>
<p class="abs slide-sub">Simple Data Collection (6 Questions)</p>
<div class="abs btn-light">&#8594;&nbsp; Read More</div>
<div class="abs scroll-down">
  <svg width="30" height="30" viewBox="0 0 30 30"><path d="M15 10v10M11.5 16.5 15 20l3.5-3.5" fill="none" stroke="#444" stroke-width="1"/></svg>
</div>

<!-- what we do -->
<div class="abs net-deco-left" role="img" aria-label="Decorative network of coloured nodes and links"></div>
<div class="abs net-deco-right" role="img" aria-label="Decorative network of coloured nodes and links"></div>
<h2 class="abs title" style="top:402px;font-size:20px">What We Do</h2>
<svg class="abs ornament" style="top:429px" viewBox="0 0 670 10">
  <line x1="263" y1="5" x2="325" y2="5" stroke="#ddd"/><line x1="345" y1="5" x2="407" y2="5" stroke="#ddd"/>
  <circle cx="333" cy="4" r="2" fill="var(--red)"/><circle cx="337" cy="6" r="2" fill="var(--blue)"/><circle cx="333" cy="7" r="1.6" fill="var(--green)"/>
</svg>
<p class="abs intro">TeamVerdexa is the first company to offer comprehensive evaluations of Employee Relationships with powerful software tools<br>for dynamic, real-time analysis and exploration. Their platform identifies employees playing key, yet hidden,<br>roles in the organization, such as Knowledge Hubs, Opinion Leaders.</p>
<div class="abs btn-outline" style="left:293px;top:498px;width:83px;height:23px;line-height:22px">&#8594;&nbsp; Read More</div>
<div class="abs rule" style="top:554px"></div>

<!-- how we help -->
<h2 class="abs title" style="top:582px;font-size:20px">How we can help their problem</h2>
<svg class="abs ornament" style="top:611px" viewBox="0 0 670 10">
  <line x1="263" y1="5" x2="325" y2="5" stroke="#ddd"/><line x1="345" y1="5" x2="407" y2="5" stroke="#ddd"/>
  <circle cx="333" cy="4" r="2" fill="var(--red)"/><circle cx="337" cy="6" r="2" fill="var(--blue)"/><circle cx="333" cy="7" r="1.6" fill="var(--green)"/>
</svg>
<div class="abs team-photo" role="img" aria-label="Photo of three smiling young men sitting behind a laptop"></div>
<ul class="abs benefits">
  <li><svg width="8" height="6" viewBox="0 0 8 6"><path d="M0 3h7M4.5.5 7 3 4.5 5.5" fill="none" stroke="var(--blue)" stroke-width=".9"/></svg>We aim to solve any problem related to employees</li>
  <li><svg width="8" height="6" viewBox="0 0 8 6"><path d="M0 3h7M4.5.5 7 3 4.5 5.5" fill="none" stroke="var(--blue)" stroke-width=".9"/></svg>Create Stronger, More Productive Teams</li>
  <li><svg width="8" height="6" viewBox="0 0 8 6"><path d="M0 3h7M4.5.5 7 3 4.5 5.5" fill="none" stroke="var(--blue)" stroke-width=".9"/></svg>Build Better Communications Pathways</li>
  <li><svg width="8" height="6" viewBox="0 0 8 6"><path d="M0 3h7M4.5.5 7 3 4.5 5.5" fill="none" stroke="var(--blue)" stroke-width=".9"/></svg>Encourage Innovation and Positive Change</li>
  <li><svg width="8" height="6" viewBox="0 0 8 6"><path d="M0 3h7M4.5.5 7 3 4.5 5.5" fill="none" stroke="var(--blue)" stroke-width=".9"/></svg>Develop and Retain Strong "Company Culture"</li>
</ul>

<!-- contact -->
<div class="abs contact"></div>
<h2 class="abs title" style="top:787px;font-size:20px">Contact Us To Get Started</h2>
<svg class="abs ornament" style="top:815px" viewBox="0 0 670 10">
  <line x1="263" y1="5" x2="325" y2="5" stroke="#ddd"/><line x1="345" y1="5" x2="407" y2="5" stroke="#ddd"/>
  <circle cx="333" cy="4" r="2" fill="var(--red)"/><circle cx="337" cy="6" r="2" fill="var(--blue)"/><circle cx="333" cy="7" r="1.6" fill="var(--green)"/>
</svg>
<p class="abs contact-lead">Contacting us to get a sales lead is the ultimate goal.</p>
<div class="abs field" style="left:136px;top:853px;width:194px;height:25px">Name*</div>
<div class="abs field" style="left:340px;top:853px;width:194px;height:25px">Email*</div>
<div class="abs field" style="left:136px;top:884px;width:398px;height:86px">Message*</div>
<div class="abs submit">&#8594;&nbsp; Submit Message</div>

<!-- footer -->
<footer>
<div class="abs footer"></div>
<h3 class="abs footer-title">Contact one of our four locations</h3>
<svg class="abs ornament" style="top:1066px" viewBox="0 0 670 10">
  <line x1="262" y1="5" x2="325" y2="5" stroke="#4a4a52"/><line x1="345" y1="5" x2="408" y2="5" stroke="#4a4a52"/>
  <circle cx="333" cy="4" r="2" fill="var(--red)"/><circle cx="337" cy="6" r="2" fill="var(--blue)"/><circle cx="333" cy="7" r="1.6" fill="var(--green)"/>
</svg>

<div class="abs office" style="left:70px">
  <div class="office-city">Cincinnati, OH</div>
  <div class="office-line"><svg width="7" height="7" viewBox="0 0 10 10"><path d="M2 1l2 2-1 1.5c.8 1.5 1.5 2.2 3 3L7.5 6l2 2-1.5 1.5C4.5 9 1 5.5.5 2.5z" fill="#9a9a9a"/></svg>513-555-0142</div>
  <div class="office-line"><svg width="7" height="6" viewBox="0 0 10 8"><rect x=".5" y=".5" width="9" height="7" fill="none" stroke="#9a9a9a"/><path d="M.5.5 5 4.5 9.5.5" fill="none" stroke="#9a9a9a"/></svg>cincinnati@teamverdexa.com</div>
</div>
<div class="abs office-divider" style="left:192px"></div>
<div class="abs office" style="left:219px">
  <div class="office-city">Denver, CO</div>
  <div class="office-line"><svg width="7" height="7" viewBox="0 0 10 10"><path d="M2 1l2 2-1 1.5c.8 1.5 1.5 2.2 3 3L7.5 6l2 2-1.5 1.5C4.5 9 1 5.5.5 2.5z" fill="#9a9a9a"/></svg>303-555-0187</div>
  <div class="office-line"><svg width="7" height="6" viewBox="0 0 10 8"><rect x=".5" y=".5" width="9" height="7" fill="none" stroke="#9a9a9a"/><path d="M.5.5 5 4.5 9.5.5" fill="none" stroke="#9a9a9a"/></svg>denver@teamverdexa.com</div>
</div>
<div class="abs office-divider" style="left:334px"></div>
<div class="abs office" style="left:354px">
  <div class="office-city">Birmingham, AL</div>
  <div class="office-line"><svg width="7" height="7" viewBox="0 0 10 10"><path d="M2 1l2 2-1 1.5c.8 1.5 1.5 2.2 3 3L7.5 6l2 2-1.5 1.5C4.5 9 1 5.5.5 2.5z" fill="#9a9a9a"/></svg>205-555-0163</div>
  <div class="office-line"><svg width="7" height="6" viewBox="0 0 10 8"><rect x=".5" y=".5" width="9" height="7" fill="none" stroke="#9a9a9a"/><path d="M.5.5 5 4.5 9.5.5" fill="none" stroke="#9a9a9a"/></svg>birmingham@teamverdexa.com</div>
</div>
<div class="abs office-divider" style="left:476px"></div>
<div class="abs office" style="left:494px">
  <div class="office-city">Chicago, IL</div>
  <div class="office-line"><svg width="7" height="7" viewBox="0 0 10 10"><path d="M2 1l2 2-1 1.5c.8 1.5 1.5 2.2 3 3L7.5 6l2 2-1.5 1.5C4.5 9 1 5.5.5 2.5z" fill="#9a9a9a"/></svg>303-555-0187</div>
  <div class="office-line"><svg width="7" height="6" viewBox="0 0 10 8"><rect x=".5" y=".5" width="9" height="7" fill="none" stroke="#9a9a9a"/><path d="M.5.5 5 4.5 9.5.5" fill="none" stroke="#9a9a9a"/></svg>chicago@teamverdexa.com</div>
</div>

<div class="abs bottom-bar"></div>
<p class="abs copyright">© 2016 TeamVerdexa. All Rights Reserved.</p>
<nav class="abs bottom-nav"><span>Home</span><span>The Hidden Value</span><span>About Us</span></nav>
<div class="abs to-top">
  <svg width="18" height="18" viewBox="0 0 18 18"><path d="M6.5 10 9 7.5 11.5 10" fill="none" stroke="#fff" stroke-width="1.2"/></svg>
</div>
</footer>

</body>
</html>
```